Tovella Fireworks needs a web design and logo

We need a web design and logo for a fireworks business in Sydney Australia, we do public display, weddings, tv, theatrical, clubs and any other organisation that wants to do something special.
Name is Marrowind Fireworks & Pyrotechnics

```html
<!DOCTYPE html>
<html lang="en">
<head>
<meta charset="utf-8">
<title>Marrowind Fireworks &amp; Pyrotechnics</title>
<link rel="stylesheet" href="https://fonts.googleapis.com/css2?family=Raleway:wght@300;400;500;600;700&family=Open+Sans:wght@400;600&display=swap">
<style>
  :root {
    --night: #241556;
    --night-deep: #120b33;
    --violet: #4a2a8a;
    --orange: #f07a14;
    --orange-dark: #e05a00;
    --orange-text: #ee7011;
    --blue: #2f8cf0;
    --blue-dark: #1167d8;
    --ink: #2b2b2b;
    --body-text: #555555;
    --rule: #dcdcdc;
    --footer: #2a1b47;
    --white: #ffffff;
  }
  * { margin: 0; padding: 0; box-sizing: border-box; }
  html, body { width: 1154px; height: 1200px; overflow: hidden; }
  body {
    position: relative;
    background: var(--white);
    font-family: "Open Sans", Arial, sans-serif;
    color: var(--body-text);
  }
  .sky-backdrop { position: absolute; left: 0; top: 0; width: 1154px; height: 430px; }
  .brand {
    position: absolute; left: 182px; top: 48px;
    font-family: "Raleway", Arial, sans-serif;
    font-weight: 500; font-size: 29px; line-height: 31px;
    color: var(--white);
  }
  .main-nav {
    position: absolute; left: 177px; top: 130px; width: 800px; height: 46px;
    display: flex;
    background: linear-gradient(to bottom, var(--orange) 0%, var(--orange-dark) 100%);
  }
  .main-nav a {
    flex: auto; display: flex; align-items: center; justify-content: center;
    font-family: "Raleway", Arial, sans-serif; font-weight: 500; font-size: 14px;
    color: var(--white); text-decoration: none; letter-spacing: 0.2px;
    border-right: 1px solid rgba(255,255,255,0.25);
  }
  .main-nav a:last-child { border-right: none; }
  .hero {
    position: absolute; left: 177px; top: 176px; width: 800px; height: 373px;
    background:
      radial-gradient(ellipse at 60% 30%, rgba(230,70,160,0.55), transparent 45%),
      radial-gradient(ellipse at 35% 75%, rgba(240,120,40,0.45), transparent 40%),
      radial-gradient(ellipse at 50% 95%, rgba(60,140,255,0.6), transparent 45%),
      linear-gradient(to bottom, #0b0f2a, #101a44);
    text-align: center; color: var(--white);
    font-family: "Raleway", Arial, sans-serif;
  }
  .hero-title { position: absolute; left: 0; right: 0; top: 142px; font-size: 35px; font-weight: 700; letter-spacing: 0.5px; }
  .hero-sub { position: absolute; left: 0; right: 0; top: 186px; font-size: 18px; font-weight: 600; }
  .hero-dots { position: absolute; left: 0; right: 0; top: 517px; display: flex; justify-content: center; gap: 3px; }
  .hero-dots span { width: 12px; height: 12px; border-radius: 50%; background: #d8d8d8; }
  .hero-dots span.active { background: #111; }
  .welcome { position: absolute; left: 177px; top: 590px; width: 800px; text-align: center; }
  .welcome h1 { font-family: "Raleway", Arial, sans-serif; font-weight: 400; font-size: 27px; color: var(--ink); margin-bottom: 10px; }
  .welcome p { font-size: 10.8px; line-height: 15px; margin-bottom: 10px; }
  .divider { position: absolute; left: 173px; top: 748px; width: 800px; height: 5px; border-top: 1px solid var(--rule); border-bottom: 1px solid var(--rule); }
  .services { position: absolute; left: 177px; top: 799px; width: 800px; height: 230px; }
  .service { position: absolute; top: 0; width: 190px; text-align: center; }
  .service-photo { width: 190px; height: 103px; }
  .service h2 { font-family: "Raleway", Arial, sans-serif; font-weight: 600; font-size: 15.5px; color: var(--orange-text); margin-top: 12px; }
  .service p { font-size: 9.5px; line-height: 15px; margin-top: 5px; }
  .read-more {
    display: inline-block; margin-top: 9px; width: 85px; height: 26px; line-height: 26px;
    border-radius: 3px; font-size: 9.5px; color: var(--white); text-decoration: none;
    background: linear-gradient(to bottom, var(--blue), var(--blue-dark));
    box-shadow: 0 1px 2px rgba(0,0,0,0.25);
  }
  .site-footer { position: absolute; left: 0; top: 1090px; width: 1154px; height: 110px; background: var(--footer); }
  .footer-nav { position: absolute; left: 182px; top: 32px; font-family: "Raleway", Arial, sans-serif; font-weight: 600; font-size: 11px; color: var(--white); }
  .footer-nav a { color: var(--white); text-decoration: none; }
  .footer-nav .sep { margin: 0 5px; }
  .copyright { position: absolute; left: 182px; top: 56px; font-size: 9px; color: #c9c3d8; }
  .social { position: absolute; left: 880px; top: 40px; display: flex; gap: 10px; }
  .social span { width: 16px; height: 16px; border-radius: 50%; background: var(--white); }
</style>
</head>
<body>
  <svg class="sky-backdrop" viewBox="0 0 1154 430" role="img" aria-label="Night sky over a harbour with bursting fireworks">
    <defs>
      <linearGradient id="skyTone" x1="0" y1="0" x2="1" y2="1">
        <stop offset="0" stop-color="#1e1456"/>
        <stop offset="0.5" stop-color="#3a2380"/>
        <stop offset="1" stop-color="#6a2a6e"/>
      </linearGradient>
    </defs>
    <path d="M0,0 H1154 V317 Q580,520 0,355 Z" fill="url(#skyTone)"/>
  </svg>

  <div class="brand">Marrowind Fireworks<br>&amp; Pyrotechnics</div>

  <nav class="main-nav">
    <a href="#">HOME</a><a href="#">ABOUT</a><a href="#">SERVICES</a><a href="#">FIREWORKS</a>
    <a href="#">SUPPORT</a><a href="#">PRICES</a><a href="#">GALLERY</a><a href="#">CONTACT</a>
  </nav>

  <section class="hero" role="img" aria-label="Colourful fireworks bursting over a city skyline at night">
    <div class="hero-title">FIREWORKS &amp; PYROTECHNICS</div>
    <div class="hero-sub">MAURIS VEL LACUS VITAE FELIS VESTIBULUM</div>
  </section>
  <div class="hero-dots"><span class="active"></span><span></span><span></span><span></span></div>

  <section class="welcome">
    <h1>Welcome to Marrowind Fireworks &amp; Pyrotechnics</h1>
    <p>In massa libero interdum nec interdum vel blandit sed nulla In ullamcorper est eget tempor cursus neque mi consectetuer mi a ultricies massa est sed nisl Class aptent taciti sociosqu ad litora torquent per conubia nostra per inceptos hymenaeos Proin nulla arcu nonummy luctus&nbsp; In massa libero interdum nec interdum vel blandit sed nulla In ullamcorper est eget tempor cursus neque mi consectetuer mi a ultricies massa est sed nisl</p>
    <p>Class aptent taciti sociosqu ad litora torquent per conubia nostra per inceptos hymenaeos Proin nulla arcu nonummy luctus dictum eget .</p>
  </section>

  <div class="divider"></div>

  <section class="services">
    <article class="service" style="left:0">
      <div class="service-photo" role="img" aria-label="Wedding couple dancing beside sparkler fountains" style="background:linear-gradient(135deg,#c9a6b8,#6d4a5e 60%,#e8d6c8)"></div>
      <h2>Weddings Fireworks</h2>
      <p>enaeos Proin nulla arcu nonummy luctus<br>In massa libero interdum nec interdum<br>vel blandit sed nulla ullamcorper</p>
      <a class="read-more" href="#">READ MORE</a>
    </article>
    <article class="service" style="left:202px">
      <div class="service-photo" role="img" aria-label="Golden fireworks bursting against a black sky" style="background:radial-gradient(ellipse at 50% 60%,#e08a20,#5a2a08 45%,#0a0604 80%)"></div>
      <h2>Theatrical Fireworks</h2>
      <p>enaeos Proin nulla arcu nonummy luctus<br>In massa libero interdum nec interdum<br>vel blandit sed nulla ullamcorper</p>
      <a class="read-more" href="#">READ MORE</a>
    </article>
    <article class="service" style="left:405px">
      <div class="service-photo" role="img" aria-label="Group of friends celebrating at a club night" style="background:linear-gradient(135deg,#3a3f5a,#8a7a70 50%,#2a2a3a)"></div>
      <h2>Clubs Pyrotechnics</h2>
      <p>enaeos Proin nulla arcu nonummy luctus<br>In massa libero interdum nec interdum<br>vel blandit sed nulla ullamcorper</p>
      <a class="read-more" href="#">READ MORE</a>
    </article>
    <article class="service" style="left:607px">
      <div class="service-photo" role="img" aria-label="Crowd watching a public fireworks display at dusk" style="background:linear-gradient(to bottom,#5a6aa8,#8a5a8a 50%,#2a1a1a)"></div>
      <h2>Public Display</h2>
      <p>enaeos Proin nulla arcu nonummy luctus<br>In massa libero interdum nec interdum<br>vel blandit sed nulla ullamcorper</p>
      <a class="read-more" href="#">READ MORE</a>
    </article>
  </section>

  <footer class="site-footer">
    <div class="footer-nav">
      <a href="#">HOME</a><span class="sep">|</span><a href="#">ABOUT</a><span class="sep">|</span><a href="#">SERVICES</a><span class="sep">|</span><a href="#">FIREWORKS</a><span class="sep">|</span><a href="#">SUPPORT</a><span class="sep">|</span><a href="#">PRICES</a><span class="sep">|</span><a href="#">GALLERY</a><span class="sep">|</span><a href="#">CONTACT</a>
    </div>
    <div class="copyright">© 2015 Company Name&nbsp; All right reserved&nbsp; Term of Use</div>
    <div class="social" aria-label="Social links"><span></span><span></span><span></span><span></span></div>
  </footer>
</body>
</html>
```